plumbers buisness card

A buisness card for a plumbing buisness
needs to have a water theme with navy blue, light blue and white
with an image of either a water drop, pipes, tools or something relating to plumbing and incorperating my buisness name as a logo

"Kettering Plumbing" is the words that need to stand out with "& gasfitting" to be smaller

spelling error on brief, "maintenance"
and also could you include my email d_kettering@mailwave.com.au

Industry/Entity Type

Plumbing

Contact Information for Business Card

Kettering Plumbing & Gasfitting

declan kettering
0432961085

specialising in
-new homes
-maitenance
-renovations

license no.
-73840

```html
<!DOCTYPE html>
<html lang="en">
<head>
<meta charset="utf-8">
<title>Kettering Plumbing &amp; Gasfitting – Business Card</title>
<link href="https://fonts.googleapis.com/css2?family=Orbitron:wght@600;800&display=swap" rel="stylesheet">
<style>
  :root {
    --page-bg: #e4e7ea;
    --card-white: #f3f5f8;
    --brand-blue: #1379c2;
    --brand-blue-light: #48a8e6;
    --brand-navy: #0b4f8a;
    --text-grey: #55585d;
    --white: #ffffff;
  }
  * { margin: 0; padding: 0; box-sizing: border-box; }
  html, body {
    width: 1200px; height: 900px; overflow: hidden;
    background: var(--page-bg);
    font-family: "Orbitron", sans-serif;
  }
  .canvas {
    width: 1200px; height: 900px;
    display: flex; flex-direction: column;
    align-items: center; justify-content: center; gap: 40px;
  }
  .card {
    position: relative;
    width: 660px; height: 385px;
    overflow: hidden;
    box-shadow: 0 10px 28px rgba(0,0,0,.18);
  }

  /* Wordmark shared */
  .wordmark { display: flex; align-items: center; gap: 16px; }
  .wordmark .mark-square {
    width: 64px; height: 64px; flex: none; border-radius: 10px;
  }
  .wordmark .name {
    display: block; font-weight: 800; font-size: 34px; line-height: 1.02;
    text-transform: uppercase; letter-spacing: 1px;
  }
  .wordmark .sub {
    display: block; font-weight: 600; font-size: 14px; margin-top: 4px;
    text-transform: uppercase; letter-spacing: 1.5px;
  }

  /* Back of card */
  .card-back { background: var(--brand-blue); }
  .card-back .water-drops {
    position: absolute; inset: 0;
    background:
      radial-gradient(ellipse at 25% 35%, rgba(255,255,255,.22) 0%, transparent 45%),
      radial-gradient(ellipse at 70% 80%, rgba(11,79,138,.55) 0%, transparent 60%),
      linear-gradient(160deg, var(--brand-blue-light) 0%, var(--brand-blue) 50%, var(--brand-navy) 100%);
  }
  .card-back .wordmark {
    position: absolute; right: 48px; bottom: 70px; color: var(--white);
  }
  .card-back .mark-square { background: var(--white); }

  /* Front of card */
  .card-front { background: var(--card-white); }
  .card-front .wordmark { position: absolute; left: 44px; top: 46px; }
  .card-front .mark-square { background: var(--brand-blue); }
  .card-front .wordmark .name { color: var(--brand-blue); }
  .card-front .wordmark .sub { color: var(--text-grey); }

  .details {
    position: absolute; left: 44px; top: 168px;
    font-weight: 600; font-size: 13px; color: var(--text-grey);
    text-transform: uppercase; line-height: 1.65; letter-spacing: .8px;
  }
  .details .person {
    font-weight: 800; font-size: 19px; color: var(--brand-blue); margin-bottom: 2px;
  }
  .details .spec-title { margin-top: 10px; }
  .details .services span { color: var(--brand-blue); }

  .card-front .water-band {
    position: absolute; left: 0; right: 0; bottom: 0; height: 58px;
    background:
      radial-gradient(ellipse at 40% 60%, rgba(255,255,255,.2) 0%, transparent 55%),
      linear-gradient(180deg, var(--brand-blue-light), var(--brand-blue) 60%, var(--brand-navy));
  }
</style>
</head>
<body>
<main class="canvas">
  <section class="card card-back" aria-label="Business card back">
    <div class="water-drops" role="img" aria-label="Photo of water droplets on a blue surface"></div>
    <div class="wordmark">
      <span class="mark-square"></span>
      <div>
        <span class="name">Kettering<br>Plumbing</span>
        <span class="sub">&amp; Gasfitting</span>
      </div>
    </div>
  </section>

  <section class="card card-front" aria-label="Business card front">
    <div class="wordmark">
      <span class="mark-square"></span>
      <div>
        <span class="name">Kettering<br>Plumbing</span>
        <span class="sub">&amp; Gasfitting</span>
      </div>
    </div>
    <div class="details">
      <p class="person">Declan Kettering</p>
      <p>0432961085 &nbsp;|&nbsp; License No. 73840</p>
      <p>d_kettering@mailwave.com.au</p>
      <p class="spec-title">Specialising in</p>
      <p class="services">- <span>New Homes</span> &nbsp;- <span>Maintenance</span> &nbsp;- <span>Renovations</span></p>
    </div>
    <div class="water-band" role="img" aria-label="Blue band with water droplets photo"></div>
  </section>
</main>
</body>
</html>
```